MRT Property - Business Cards

Looking for a business card & general letterhead, signage etc design for our new logo.

Colours:
000a20
0056a2
00b5ef
0088ce
68cef2

Fonts:
Poppins
Karla

Please keep look and feel of new brand - example in the zip package I sent.

```html
<!DOCTYPE html>
<html lang="en">
<head>
<meta charset="utf-8">
<title>MRT Property – Business Cards</title>
<link rel="stylesheet" href="https://fonts.googleapis.com/css2?family=Poppins:wght@400;500;600;700&display=swap">
<style>
  :root {
    --ink-navy: #000a20;
    --card-navy: #10142c;
    --card-navy-deep: #0b0f24;
    --brand-blue: #0056a2;
    --brand-mid: #0088ce;
    --brand-cyan: #00b5ef;
    --brand-sky: #68cef2;
    --pattern-violet: #3d4a8f;
    --text-light: #e9edf7;
    --stage: #2a2b2f;
  }
  * { box-sizing: border-box; margin: 0; padding: 0; }
  html, body {
    width: 1200px; height: 900px; overflow: hidden;
    background: var(--stage);
    font-family: "Poppins", sans-serif;
  }
  .sheet {
    position: relative; width: 1200px; height: 900px;
    display: flex; flex-direction: column; align-items: center; justify-content: center; gap: 40px;
  }
  .card {
    position: relative; width: 700px; height: 400px;
    border-radius: 18px; overflow: hidden;
    background: var(--card-navy);
    box-shadow: 0 18px 40px rgba(0,0,0,.45);
  }
  .card__edge {
    position: absolute; left: 0; right: 0; bottom: 0; height: 12px;
    background: var(--brand-blue);
  }

  /* Back of card */
  .card--back .card__pattern {
    position: absolute; inset: 0;
    background: linear-gradient(120deg, var(--pattern-violet) 0%, #232a5a 35%, var(--card-navy-deep) 75%);
  }
  .card--back .card__wordmark {
    position: absolute; right: 70px; bottom: 70px;
    font-weight: 600; font-size: 34px; letter-spacing: .5px;
    color: var(--text-light);
  }

  /* Front of card */
  .card--front {
    background: linear-gradient(135deg, var(--card-navy) 0%, var(--card-navy-deep) 100%);
  }
  .card__wordmark-large {
    position: absolute; left: 48px; top: 48px;
    font-weight: 700; font-size: 64px; line-height: 1;
    color: var(--brand-blue);
  }
  .person { position: absolute; left: 52px; top: 150px; }
  .person__name { font-weight: 700; font-size: 28px; color: var(--brand-mid); line-height: 1.1; }
  .person__role { font-size: 15px; color: var(--text-light); margin-top: 4px; }
  .address { position: absolute; left: 52px; top: 228px; font-size: 14px; line-height: 1.4; color: var(--text-light); }
  .contacts { position: absolute; left: 52px; top: 290px; list-style: none; }
  .contacts li {
    display: flex; align-items: center; gap: 10px;
    font-size: 14px; line-height: 24px; color: var(--text-light);
  }
  .contacts svg { width: 14px; height: 14px; fill: var(--brand-mid); flex: none; }
</style>
</head>
<body>
<main class="sheet">
  <section class="card card--back" aria-label="Business card, back">
    <div class="card__pattern" role="img" aria-label="Repeating brand pattern in violet to deep navy"></div>
    <div class="card__wordmark">MRT Property</div>
    <div class="card__edge"></div>
  </section>

  <section class="card card--front" aria-label="Business card, front">
    <div class="card__wordmark-large">MRT Property</div>
    <div class="person">
      <p class="person__name">Daniel Reyes</p>
      <p class="person__role">Managing Director</p>
    </div>
    <p class="address">48 Cedar Hollow Lane<br>Ridgeland, MS 39157</p>
    <ul class="contacts">
      <li>
        <svg viewBox="0 0 24 24" aria-hidden="true"><path d="M6.6 10.8a15.1 15.1 0 0 0 6.6 6.6l2.2-2.2a1 1 0 0 1 1-.25 11.4 11.4 0 0 0 3.6.57 1 1 0 0 1 1 1V20a1 1 0 0 1-1 1A17 17 0 0 1 3 4a1 1 0 0 1 1-1h3.5a1 1 0 0 1 1 1c0 1.25.2 2.45.57 3.57a1 1 0 0 1-.25 1z"/></svg>
        555.214.7730
      </li>
      <li>
        <svg viewBox="0 0 24 24" aria-hidden="true"><path d="M2 5h20v14H2zm2 2v.5l8 5 8-5V7l-8 5z"/></svg>
        info@mrtproperty.com
      </li>
      <li>
        <svg viewBox="0 0 24 24" aria-hidden="true"><circle cx="12" cy="12" r="10"/></svg>
        www.mrtproperty.com
      </li>
    </ul>
    <div class="card__edge"></div>
  </section>
</main>
</body>
</html>
```